Corvel Capital LLC

Need Professional Business cards for New Investment Fund

Target Market(s)

High Quality investors

Industry/Entity Type

Financial

Contact Information for Business Card

Phone Number +1 555 284 6190
Name Lukas Varenko
Title Fund Manager
email lv@FundCorvel.com
Website www.FundCorvel.com

Colors

Designer to choose colors to be used in the design.

Requirements
Must have
• Must have our Logo and all of the above. Must be made so lettering and loge can be raised

```html
<!DOCTYPE html>
<html lang="en">
<head>
<meta charset="utf-8">
<title>Quilvane — Business Card</title>
<link href="https://fonts.googleapis.com/css2?family=Jost:wght@400;500;600&family=Lato:wght@400&display=swap" rel="stylesheet">
<style>
  :root {
    --page-bg: #2a2b2d;
    --card-bg: #1b1c1e;
    --card-back: #161718;
    --accent: #35e21b;
    --muted: #e6e6e6;
    --text: #ffffff;
    --rule: #5a5b5e;
    --mark-grey: #4b4d50;
  }
  html, body {
    margin: 0;
    width: 1200px;
    height: 1108px;
    overflow: hidden;
    background: var(--page-bg);
  }
  .sheet {
    position: relative;
    width: 1200px;
    height: 1108px;
    display: flex;
    justify-content: center;
    align-items: center;
    gap: 70px;
  }
  .card {
    width: 400px;
    height: 640px;
    border-radius: 26px;
    position: relative;
    overflow: hidden;
    box-shadow: 0 18px 40px rgba(0,0,0,0.45);
  }
  .card-front {
    background: var(--card-bg);
    text-align: center;
    font-family: "Lato", sans-serif;
  }
  .brand {
    position: absolute;
    top: 170px;
    left: 0;
    right: 0;
    display: flex;
    justify-content: center;
    align-items: center;
    gap: 14px;
  }
  .brand-dot {
    width: 20px;
    height: 20px;
    border-radius: 50%;
    background: var(--accent);
  }
  .brand-name {
    font-family: "Jost", sans-serif;
    font-weight: 500;
    font-size: 50px;
    letter-spacing: 2px;
    color: var(--accent);
  }
  .holder {
    position: absolute;
    top: 400px;
    left: 0;
    right: 0;
  }
  .holder-name {
    font-family: "Jost", sans-serif;
    font-weight: 600;
    font-size: 27px;
    color: var(--accent);
    text-transform: uppercase;
    letter-spacing: 0.5px;
  }
  .holder-title {
    font-family: "Jost", sans-serif;
    font-weight: 400;
    font-size: 20px;
    color: var(--muted);
    margin-top: 2px;
  }
  .icon-rule {
    display: flex;
    align-items: center;
    justify-content: center;
    gap: 8px;
    margin: 12px 30px 8px;
  }
  .icon-rule .line {
    flex: 1;
    height: 1px;
    background: var(--rule);
  }
  .icon-rule svg { display: block; }
  .contact {
    font-size: 20px;
    line-height: 27px;
    color: var(--text);
  }
  .card-back { background: var(--card-back); }
  .pattern-field {
    position: absolute;
    inset: 0;
    background: linear-gradient(160deg, #202123 0%, #18191a 55%, #141516 100%);
  }
  .back-brand {
    position: absolute;
    right: 70px;
    bottom: 150px;
    font-family: "Jost", sans-serif;
    font-weight: 500;
    font-size: 24px;
    color: var(--mark-grey);
    letter-spacing: 1px;
  }
</style>
</head>
<body>
<main class="sheet">
  <section class="card card-front">
    <div class="brand">
      <span class="brand-dot"></span>
      <span class="brand-name">Quilvane</span>
    </div>
    <div class="holder">
      <div class="holder-name">Lukas Varenko</div>
      <div class="holder-title">Fund Manager</div>
      <div class="icon-rule">
        <span class="line"></span>
        <svg width="26" height="26" viewBox="0 0 26 26" aria-label="Phone">
          <circle cx="13" cy="13" r="13" fill="var(--accent)"/>
          <path d="M8 7.5l3 0 1.2 3-1.7 1.2a7 7 0 0 0 3.8 3.8l1.2-1.7 3 1.2 0 3a1.5 1.5 0 0 1-1.6 1.5A11 11 0 0 1 6.5 9.1 1.5 1.5 0 0 1 8 7.5z" fill="#1b1c1e"/>
        </svg>
        <svg width="26" height="26" viewBox="0 0 26 26" aria-label="Email">
          <circle cx="13" cy="13" r="13" fill="var(--accent)"/>
          <rect x="6.5" y="8.5" width="13" height="9" rx="1" fill="#1b1c1e"/>
          <path d="M7 9l6 5 6-5" fill="none" stroke="var(--accent)" stroke-width="1.3"/>
        </svg>
        <svg width="26" height="26" viewBox="0 0 26 26" aria-label="Location">
          <circle cx="13" cy="13" r="13" fill="var(--accent)"/>
          <path d="M13 6a4.8 4.8 0 0 0-4.8 4.8c0 3.6 4.8 9 4.8 9s4.8-5.4 4.8-9A4.8 4.8 0 0 0 13 6z" fill="#1b1c1e"/>
          <circle cx="13" cy="10.8" r="1.8" fill="var(--accent)"/>
        </svg>
        <span class="line"></span>
      </div>
      <div class="contact">
        <div>+1 555 284 6190</div>
        <div>lv@FundCorvel.com</div>
        <div>www.FundCorvel.com</div>
      </div>
    </div>
  </section>

  <section class="card card-back">
    <div class="pattern-field" role="img" aria-label="Tonal repeating brand pattern, dark grey on black"></div>
    <div class="back-brand">Quilvane</div>
  </section>
</main>
</body>
</html>
```